Commercial, Public Works, Contractor needs a modern web design

We are a General and Engineering contracting firm with vast experience in our industry. Our focus is on Commercial, Tenant Improvement, Restaurants, and Public Works. We are opening a new business and would like that excitement and energy to show through the new web design. The colors we like are black, red and grey, we are open to color ideas. Attached is our logo design.

Industry/Entity Type

Restaurant

```html
<!DOCTYPE html>
<html lang="en">
<head>
<meta charset="utf-8">
<title>Halvorsen Builders</title>
<link rel="stylesheet" href="https://fonts.googleapis.com/css2?family=Roboto:wght@300;400;500;700&family=Oswald:wght@400;500&family=Montserrat:wght@500;600&display=swap">
<style>
:root{
  --red:#c8101c;
  --red-dark:#a40b14;
  --ink:#2b2b2b;
  --grey:#6b6b6b;
  --light:#f2f2f2;
  --black:#0a0a0a;
  --bar:#2e2e2e;
}
*{margin:0;padding:0;box-sizing:border-box}
html,body{width:798px;height:1200px;overflow:hidden;background:#fff}
body{position:relative;font-family:'Roboto',sans-serif;color:var(--ink)}
h1,h2,h3{font-weight:400}
.abs{position:absolute;white-space:nowrap}
.wrap{white-space:normal}
.sketch{background:linear-gradient(180deg,#fafafa,#e9e9e9)}
.sketch-left{left:0;top:56px;width:114px;height:374px}
.sketch-right{left:684px;top:240px;width:114px;height:190px}
.phone{left:116px;top:40px;font-size:14px;display:flex;align-items:center;gap:6px;color:#222}
.brand{left:299px;top:40px;width:200px;font-weight:700;font-size:12px;color:var(--red);letter-spacing:.5px;display:flex;align-items:center;justify-content:center;gap:5px}
.brand i{width:10px;height:10px;border-radius:50%;background:var(--red);display:inline-block}
.social{left:594px;top:35px;display:flex;gap:5px}
.social span{width:19px;height:19px;border-radius:50%;border:2px solid #ddd}
.nav{left:114px;top:89px;width:570px;height:40px;background:linear-gradient(#d8141f,var(--red-dark));display:flex}
.nav a{color:#fff;text-decoration:none;font-size:11px;line-height:40px;text-align:center;border-right:1px solid rgba(0,0,0,.25);white-space:nowrap}
.nav a:last-child{border-right:0}
.nav a.active{background:linear-gradient(#3a3a3a,#1a1a1a)}
.hero{left:114px;top:129px;width:570px;height:301px;background:linear-gradient(160deg,#6f8fb7,#c8d6e8 55%,#e6ecf4)}
.hero-caption{left:116px;top:376px;width:348px;height:54px;background:rgba(40,40,40,.72);color:#fff;font-family:'Oswald',sans-serif;font-size:19px;line-height:54px;padding-left:20px}
.hero-arrows{left:632px;top:398px;display:flex}
.hero-arrows span{width:18px;height:18px;display:flex;align-items:center;justify-content:center}
.hero-arrows .prev{background:var(--red)}
.hero-arrows .next{background:#333}
.hero-shadow{left:150px;top:430px;width:500px;height:20px;background:radial-gradient(ellipse at top,rgba(0,0,0,.12),transparent 70%)}
.welcome-title{left:0;top:462px;width:798px;text-align:center;font-family:'Montserrat',sans-serif;font-weight:500;font-size:14px;color:#222}
.welcome-title em{font-style:normal;color:var(--red);font-weight:600}
.welcome-text{left:114px;top:488px;width:570px;text-align:center;font-size:9.2px;line-height:14.4px;color:var(--grey)}
.btn-red{left:364px;top:547px;width:70px;height:22px;background:var(--red);color:#fff;border-radius:2px;font-size:9.5px;text-align:center;line-height:22px}
.card{top:590px;width:137px;height:155px;background:#fff;border:1px solid #ddd;box-shadow:0 6px 8px -6px rgba(0,0,0,.3);white-space:normal}
.card .pic{height:94px}
.card h3{font-size:9.4px;font-weight:500;color:var(--red);margin:11px 0 0 9px}
.card p{font-size:6.6px;line-height:12px;color:#555;margin:4px 8px 0 9px}
.know-kicker{left:114px;top:792px;font-size:17.6px;font-weight:500;color:var(--red)}
.know-title{left:114px;top:819px;font-size:20px;font-weight:400;color:#222}
.know-text{left:114px;top:850px;width:236px;font-size:7.6px;line-height:13.6px;color:#444}
.know-text p+p{margin-top:7px}
.btn-outline{left:114px;top:936px;width:64px;height:22px;border:1px solid #bbb;border-radius:2px;font-size:7.6px;text-align:center;line-height:20px;color:#222}
.news-title{left:381px;top:788px;font-size:13.6px;font-weight:400;color:#222}
.news-title em{font-style:normal;color:var(--red)}
.news{top:815px;width:144px;white-space:normal}
.news .pic{height:95px}
.news .date{font-size:8px;color:var(--red);margin-top:9px}
.news p{font-size:7.4px;line-height:13px;color:#444;margin-top:5px}
.footer{left:0;top:1001px;width:798px;height:149px;background:var(--black)}
.f-head{font-size:10.5px;color:#fff}
.f-text{font-size:7.8px;line-height:13.5px;color:#ddd}
.signup{left:256px;top:1084px;width:176px;height:29px;display:flex}
.signup .field{flex:1;border:1px solid #333;background:#111;color:#666;font-size:7px;line-height:27px;padding-left:8px}
.signup .go{width:50px;background:var(--red);color:#fff;font-size:10.5px;text-align:center;line-height:29px}
.map{left:481px;top:1018px;width:203px;height:106px;background:linear-gradient(135deg,#ece8e0,#dcd7cd)}
.bottom{left:0;top:1150px;width:798px;height:50px;background:var(--bar)}
.copy{left:116px;top:1169px;font-size:7.4px;color:#eee}
.follow{left:560px;top:1166px;font-size:9.6px;font-weight:500;color:#fff;display:flex;align-items:center;gap:6px}
.follow span{width:18px;height:18px;border:1.5px solid #ddd;border-radius:50%}
</style>
</head>
<body>
<div class="abs sketch sketch-left" role="img" aria-label="Faint line sketch of a construction crane"></div>
<div class="abs sketch sketch-right" role="img" aria-label="Faint line sketch of an excavator"></div>

<div class="abs phone">
  <svg width="11" height="11" viewBox="0 0 12 12"><rect width="12" height="12" rx="2" fill="#c8101c"/><path d="M3.5 2.8c.4-.3.8-.2 1 .2l.6 1.1c.2.3.1.6-.2.8l-.4.3c.4.9 1.1 1.6 2 2l.3-.4c.2-.3.5-.4.8-.2l1.1.6c.4.2.5.6.2 1-.6.8-1.4.9-2.3.5C5 8 4 7 3.2 5.4 2.8 4.5 2.9 3.4 3.5 2.8z" fill="#fff"/></svg>
  310.555.0148
</div>
<div class="abs brand"><i></i>HALVORSEN BUILDERS</div>
<div class="abs social"><span></span><span></span><span></span><span></span></div>

<nav class="abs nav">
  <a class="active" style="width:69px">HOME</a><a style="width:83px">ABOUT US</a><a style="width:100px">OUR PRODUCT</a><a style="width:131px">MEDIA/CUSTOMERS</a><a style="width:81px">SERVICES</a><a style="width:106px">CONTACT US</a>
</nav>

<div class="abs hero" role="img" aria-label="Two engineers in hard hats reviewing blueprints in front of office towers"></div>
<div class="abs hero-caption">GENERAL ENGINEERING CONTRACTING FIRM</div>
<div class="abs hero-arrows">
  <span class="prev"><svg width="6" height="8" viewBox="0 0 6 8"><path d="M4.5 1 1.5 4l3 3" stroke="#fff" stroke-width="1.3" fill="none"/></svg></span>
  <span class="next"><svg width="6" height="8" viewBox="0 0 6 8"><path d="M1.5 1l3 3-3 3" stroke="#fff" stroke-width="1.3" fill="none"/></svg></span>
</div>
<div class="abs hero-shadow"></div>

<h1 class="abs welcome-title">WELCOME TO <em>GENERAL ENGINEERING CONTRACTING FIRM</em></h1>
<p class="abs wrap welcome-text">Lorem Ipsum has been the industry's standard dummy text ever since the 1500s, when an unknown printer took a galley of type and scrambled it to make a type specimen book. It has survived not only five centuries, but also the leap into electronic typesetting, remaining essentially unchanged. It was popularised in the 1960s with the release of Letraset sheets containing Lorem Ipsum passages</p>
<div class="abs btn-red">Read More</div>

<div class="abs card" style="left:116px"><div class="pic" role="img" aria-label="Modern glass office building lit at dusk" style="background:linear-gradient(#2f5fc4,#1b2f66 60%,#c78b3c)"></div><h3>COMMERCIAL</h3><p>Lorem Ipsum is simply dummy text of the printing and typesetting industry</p></div>
<div class="abs card" style="left:258px"><div class="pic" role="img" aria-label="Glass skyscrapers seen from below" style="background:linear-gradient(120deg,#c9d4e0,#3c4a5c)"></div><h3>TENANT IMPROVEMENT</h3><p>Lorem Ipsum is simply dummy text of the printing and typesetting industry</p></div>
<div class="abs card" style="left:401px"><div class="pic" role="img" aria-label="Restaurant building with brick and steel facade" style="background:linear-gradient(135deg,#b5553a,#d9d6d2 55%,#444)"></div><h3>RESTAURANTS</h3><p>Lorem Ipsum is simply dummy text of the printing and typesetting industry</p></div>
<div class="abs card" style="left:544px"><div class="pic" role="img" aria-label="Contractors shaking hands on a work site" style="background:linear-gradient(135deg,#d5dde6,#8aa0b8)"></div><h3>PUBLIC WORKS</h3><p>Lorem Ipsum is simply dummy text of the printing and typesetting industry</p></div>

<h2 class="abs know-kicker">GET TO KNOW MORE</h2>
<h3 class="abs know-title">Engineering contracting</h3>
<div class="abs wrap know-text">
  <p>Nemo enim ipsam voluptatem quia voluptas sit aspernatur aut odit aut fugit, sed quia consequuntur magni dolores eos qui ratione voluptatem sequi nesciunt. Neque porro</p>
  <p>Nemo enim ipsam voluptatem quia voluptas sit aspernatur aut odit aut fugit, sed quia consequuntur magni</p>
</div>
<div class="abs btn-outline">READ MORE</div>

<h2 class="abs news-title">Latest <em>News</em></h2>
<div class="abs news" style="left:382px"><div class="pic" role="img" aria-label="Row of brick townhouses under a blue sky" style="background:linear-gradient(#dfe8f2,#9b6a58 60%,#7c8a55)"></div><div class="date">17/Sep/2015</div><p>Lorem ipsum dolor sit amet, nsectetuer adipiscing elit, sed diam</p></div>
<div class="abs news" style="left:542px"><div class="pic" role="img" aria-label="Apartment building against a bright blue sky" style="background:linear-gradient(#2d6fd0,#7fa9e0 50%,#a8744e)"></div><div class="date">17/Sep/2015</div><p>Lorem ipsum dolor sit amet, nsectetuer adipiscing elit, sed diam</p></div>

<footer class="abs footer"></footer>
<div class="abs f-head" style="left:114px;top:1017px">ADDRESS</div>
<div class="abs f-text" style="left:115px;top:1042px">LINDENALLEE 14 · 40211<br>Düsseldorf DE</div>
<div class="abs f-head" style="left:115px;top:1076px">TELEPHONE</div>
<div class="abs f-text" style="left:116px;top:1096px;font-size:8.6px;line-height:17px">+ 49 151. 555 010 22 ·<br>info@halvorsenbuild.com</div>
<div class="abs f-head" style="left:256px;top:1017px">NEWSLETTER</div>
<div class="abs wrap f-text" style="left:257px;top:1040px;width:180px;font-size:6.9px;line-height:12.5px">Excepteur sint occaecat cupidatat non proident, sunt in culpa qui officia deserunt mollit anim id est laborum.</div>
<div class="abs signup"><div class="field">Enter Email</div><div class="go">Sign Up</div></div>
<div class="abs map" role="img" aria-label="Street map showing the office location with a red pin"></div>

<div class="abs bottom"></div>
<div class="abs copy">© 2015 . All rights reserved.</div>
<div class="abs follow">Follow us :&nbsp;<span></span><span></span><span></span></div>
</body>
</html>
```